Flyer for photo scanning business

Hello,
I need a flyer created for my business that would be suitable for print, to drop in letterboxes in my local community.

I would like the flyer to convey very simply the services I offer which is scanning negatives, slides and VHS tapes to digital files.
Hopefully it can make it look like an easy process, as people are often daunted by the task of sorting through old photos so they don't always get around to having them scanned.

I have a pinned facebook post that can be used by the designer to reference my services. Pricing does not need to be included on the flyer.
http://facebook.com/lanternvaultmedia

Target Market(s)

Parents & Grandparents

Requirements
Must have
• Must make my services look simple! Refer to pinned facebook post for detailed outline of my services.

I would like to flyer to point towards my contact details -
www.lanternvault.com
Miriam 0482 917 336

Colours in line with my logo/brand (uploaded to brief).
Nice to have
• Stock images of 35mm film negatives, 8mm film, VHS tapes, or Brightfane slides would be worth including. I have also uploaded a mockup of the USB sticks that I provide with digitised images.
Should not have
• no prices needed,

```html
<!DOCTYPE html>
<html lang="en">
<head>
<meta charset="utf-8">
<title>Lanternvault Media – Scanning Flyer</title>
<link href="https://fonts.googleapis.com/css2?family=Open+Sans:wght@400;600&family=Raleway:wght@300;400&family=Tinos&display=swap" rel="stylesheet">
<style>
  :root{
    --ink:#050608;
    --blue:#2f7fc6;
    --blue-deep:#1f5f9e;
    --sky:#e4ecf5;
    --paper:#f7f9fc;
    --text:#2a2d33;
    --white:#ffffff;
    --stage:#d9dadc;
  }
  *{box-sizing:border-box;margin:0;padding:0}
  html,body{width:1200px;height:801px;overflow:hidden;background:var(--stage)}
  .flyer{position:absolute;left:300px;top:12px;width:600px;height:776px;overflow:hidden;
    background:linear-gradient(160deg,var(--sky) 0%,var(--paper) 45%,var(--sky) 75%,var(--white) 100%);
    box-shadow:0 4px 14px rgba(0,0,0,.28);font-family:'Tinos',serif;color:var(--text)}
  .hero{position:absolute;left:0;top:0;width:600px;height:296px}
  .brand{position:absolute;left:18px;top:26px;display:flex;align-items:center;gap:10px;
    font-family:'Open Sans',sans-serif;font-weight:400;color:var(--white);font-size:20px;letter-spacing:2px}
  .brand-dot{width:30px;height:30px;border-radius:50%;border:2px solid var(--blue)}
  .intro{position:absolute;left:18px;top:89px;width:320px;font-family:'Open Sans',sans-serif;font-size:12.5px;line-height:18px;color:var(--white)}
  .intro-sub{position:absolute;left:20px;top:125px;font-size:10.5px;color:var(--white);font-family:'Tinos',serif}
  .benefits{position:absolute;left:18px;top:153px;list-style:none}
  .benefits li{display:flex;align-items:center;gap:8px;height:28.5px;font-family:'Open Sans',sans-serif;
    font-size:15px;letter-spacing:.6px;color:#7cc2f0;text-transform:uppercase}
  .benefits svg{width:22px;height:22px;stroke:var(--white);fill:none;stroke-width:1.3}
  .headline{position:absolute;left:60px;top:303px;width:480px;text-align:center;font-family:'Raleway',sans-serif;
    font-weight:400;font-size:19px;line-height:22px;color:var(--ink)}
  .promise{position:absolute;left:18px;top:387px;width:240px;font-family:'Raleway',sans-serif;font-size:11.5px;line-height:14px;color:var(--blue-deep)}
  .step{position:absolute;left:18px;width:240px;display:flex;gap:6px}
  .step svg{flex:none;width:42px;height:42px;stroke:var(--blue-deep);fill:none;stroke-width:1.4}
  .step h3{font-family:'Raleway',sans-serif;font-weight:400;font-size:13.5px;color:var(--blue-deep);line-height:14px}
  .step p{font-size:8.6px;line-height:11.6px;text-align:justify}
  .step-1{top:447px}.step-2{top:522px}.step-3{top:611px}
  .archive-photo{position:absolute;left:298px;top:389px;width:302px;height:151px}
  .tech{position:absolute;left:298px;top:550px;width:266px}
  .tech h2{font-family:'Raleway',sans-serif;font-weight:400;font-size:16.5px;color:var(--blue-deep);margin-bottom:6px}
  .tech p{font-size:8.6px;line-height:11.8px;text-align:justify;margin-bottom:4px}
  .footer{position:absolute;left:0;top:710px;width:600px;height:66px}
  .contact{position:absolute;left:18px;top:718px;font-family:'Raleway',sans-serif;color:var(--white);font-size:16px;line-height:23px}
  .contact div{display:flex;align-items:center;gap:8px}
  .contact svg{width:13px;height:13px;stroke:#7cc2f0;fill:none;stroke-width:1.3}
</style>
</head>
<body>
<main class="flyer">
  <svg class="hero" viewBox="0 0 600 296" aria-hidden="false">
    <defs>
      <linearGradient id="wood" x1="0" y1="0" x2="1" y2="1">
        <stop offset="0" stop-color="#8a4a22"/><stop offset=".45" stop-color="#c98a4c"/>
        <stop offset=".7" stop-color="#2a2e38"/><stop offset="1" stop-color="#b0602a"/>
      </linearGradient>
    </defs>
    <rect x="250" y="0" width="350" height="290" fill="url(#wood)" role="img" aria-label="Photo of old VHS tapes and film boxes on a wooden table"/>
    <polygon points="0,0 420,0 296,290 0,290" fill="var(--blue)"/>
    <polygon points="0,0 410,0 286,290 0,290" fill="var(--ink)"/>
    <rect x="0" y="288" width="600" height="5" fill="#6ea6d8"/>
  </svg>

  <div class="brand"><span class="brand-dot"></span>LANTERNVAULT MEDIA</div>
  <p class="intro">Do you have a pile of old slides or photo negatives laying around collecting dust?</p>
  <p class="intro-sub">Here’s what my scanning services can do for your old photos:</p>
  <ul class="benefits">
    <li><svg viewBox="0 0 24 24"><rect x="2" y="3" width="20" height="18"/><path d="M5 12c3-4 11-4 14 0c-3 4-11 4-14 0z"/><circle cx="12" cy="12" r="2"/></svg>View easily</li>
    <li><svg viewBox="0 0 24 24"><path d="M2 6h7l2 2h10v12H2z"/><path d="M2 11h19"/></svg>Store safely</li>
    <li><svg viewBox="0 0 24 24"><circle cx="8" cy="7" r="3"/><circle cx="16" cy="7" r="3"/><path d="M3 21v-5a5 5 0 0 1 10 0v5M11 21v-5a5 5 0 0 1 10 0v5"/></svg>Share with family</li>
    <li><svg viewBox="0 0 24 24"><rect x="6" y="2" width="12" height="6"/><rect x="2" y="8" width="20" height="9"/><rect x="6" y="14" width="12" height="8"/></svg>Print copies</li>
  </ul>

  <h1 class="headline">I use high end equipment and my unique technical skills as a TV &amp; Broadcast professional to digitise photo negatives, slides and video tapes.</h1>

  <p class="promise">I promise to make it very easy for you to keep your precious memories forever.</p>

  <div class="step step-1">
    <svg viewBox="0 0 42 42"><rect x="1" y="8" width="40" height="28"/><rect x="8" y="13" width="26" height="18"/><path d="M3 11h3M3 33h3M36 11h3M36 33h3M12 10v1M18 10v1M24 10v1M30 10v1M12 33v1M18 33v1M24 33v1M30 33v1"/></svg>
    <div><h3>Step 1</h3><p>Find your old negatives or tapes and organise them as much or as little as you want.</p></div>
  </div>
  <div class="step step-2">
    <svg viewBox="0 0 42 42"><rect x="12" y="6" width="28" height="18"/><path d="M12 6l14 11l14-11"/><path d="M4 16c-4 6 2 18 12 22l4-5-5-4-3 3c-3-2-5-6-5-9l3-2-3-5z"/></svg>
    <div><h3>Step 2</h3><p>email miriam@lanternvault.com or contact me and I will come and collect these from your home in the hills area.</p></div>
  </div>
  <div class="step step-3">
    <svg viewBox="0 0 42 42"><rect x="3" y="7" width="36" height="32"/><path d="M3 14h36M10 3v7M32 3v7"/><circle cx="21" cy="27" r="8"/><path d="M17 27l3 3 5-6"/></svg>
    <div><h3>Step 3</h3><p>Once completed (usually within a few days) I will drop back your box of memories with a USB stick containing high resolution JPEG files. Contactless payment will be processed when I arrive.</p></div>
  </div>

  <svg class="archive-photo" viewBox="0 0 302 151">
    <defs>
      <linearGradient id="slides" x1="0" y1="0" x2="1" y2="0">
        <stop offset="0" stop-color="#1c1f2a"/><stop offset=".45" stop-color="#3a3c44"/>
        <stop offset=".6" stop-color="#2f6fb4"/><stop offset=".8" stop-color="#d9a22a"/><stop offset="1" stop-color="#c2282a"/>
      </linearGradient>
    </defs>
    <polygon points="10,0 302,0 302,151 0,151 0,10" fill="var(--blue-deep)"/>
    <polygon points="13,4 302,4 302,147 3,147 3,13" fill="url(#slides)" role="img" aria-label="Photo of film canisters, negatives and coloured slide mounts"/>
  </svg>

  <section class="tech">
    <h2>Technical Things</h2>
    <p>Every frame is physically cleaned and examined before scanning to ensure the best possible result. I then use an additional infra-red scanning technique to further reduce dust and scratches.</p>
    <p>JPEG files are supplied at 2400 dpi which means you can easily print or enlarge your photos. They also look great on a 4k screen!</p>
    <p>VHS tapes are upscaled and captured at HD 1080p in a 100% digital workflow ensuring the best possibly quality and playback on your computer.</p>
  </section>

  <svg class="footer" viewBox="0 0 600 66">
    <path d="M248 0C268 0 278 12 292 32C302 47 310 53 334 53H600" fill="none" stroke="var(--blue)" stroke-width="3"/>
    <path d="M0 0H244C264 0 272 14 286 34C296 48 304 56 330 56H600V66H0Z" fill="var(--ink)"/>
  </svg>
  <div class="contact">
    <div><svg viewBox="0 0 14 14"><circle cx="7" cy="7" r="6"/><path d="M1 7h12M7 1c-3 3-3 9 0 12M7 1c3 3 3 9 0 12"/></svg>www.lanternvault.com</div>
    <div><svg viewBox="0 0 14 14"><path d="M2 2c-2 4 3 10 8 11l2-2-3-3-2 1c-2-1-3-3-3-4l1-2-3-3z"/></svg>0482 917 336</div>
  </div>
</main>
</body>
</html>
```